Business Card Design for Occupational Medicine Start Up Company

We need to design a professional business card. We are a healthcare company providing occupational medicine services to blue collar industries. We are professional, efficient and high quality service providers.

Target Market(s)

Blue Collar Industry: Shipbuilding, Ports, Trucking Companies; The Executives and Safety Officers for these companies

Industry/Entity Type

Healthcare

Contact Information for Business Card

Logo, Name, Title, Email, Phone

Other font styles liked:
• Please match our Brand Guide

Requirements
Must have
• Our Company Colors and Logo

```html
<!DOCTYPE html>
<html lang="en">
<head>
<meta charset="utf-8">
<title>CrewWell Business Card</title>
<link rel="stylesheet" href="https://fonts.googleapis.com/css2?family=Montserrat:wght@400;700&family=Roboto:wght@400&display=swap">
<style>
  :root {
    --backdrop: #e4e3e1;
    --card: #1b1c1f;
    --edge: #e8a74c;
    --brand-blue: #2b3a94;
    --text-light: #f2f2f2;
    --icon-blue: #3a4fb8;
  }
  * { margin: 0; padding: 0; box-sizing: border-box; }
  html, body {
    width: 1200px; height: 801px; overflow: hidden;
    background: radial-gradient(ellipse at 50% 40%, #efeeec 0%, var(--backdrop) 60%, #cfcecb 100%);
  }
  .sheet {
    position: relative; width: 1200px; height: 801px;
    display: flex; align-items: center; justify-content: center; gap: 44px;
  }
  .card {
    position: relative; width: 530px; height: 303px;
    background: var(--card);
    border: 2px solid var(--edge);
    box-shadow: 0 18px 40px rgba(0,0,0,0.28);
    overflow: hidden;
  }
  .name-block {
    position: absolute; top: 34px; right: 58px; text-align: right;
  }
  .name-block .name {
    font-family: "Montserrat", sans-serif; font-weight: 700;
    font-size: 25px; letter-spacing: 1px; color: var(--brand-blue);
  }
  .name-block .title {
    font-family: "Roboto", sans-serif; font-size: 15px;
    color: var(--text-light); margin-top: 4px;
  }
  .corner-square {
    position: absolute; top: 0; right: 0; width: 34px; height: 38px;
    background: var(--brand-blue);
  }
  .brand {
    display: flex; align-items: center; gap: 12px;
    font-family: "Montserrat", sans-serif; font-weight: 700;
    color: var(--brand-blue); letter-spacing: 1.5px;
  }
  .brand .mark {
    width: 18px; height: 18px; border-radius: 50%; background: var(--brand-blue);
  }
  .front .brand { position: absolute; left: 40px; top: 128px; font-size: 30px; }
  .contacts {
    position: absolute; left: 40px; bottom: 32px; list-style: none;
    font-family: "Roboto", sans-serif; font-size: 15px; color: var(--text-light);
  }
  .contacts li { display: flex; align-items: center; gap: 9px; line-height: 23px; }
  .contacts svg { width: 12px; height: 12px; fill: var(--icon-blue); flex: none; }
  .back .brand { position: absolute; right: 46px; bottom: 78px; font-size: 36px; }
</style>
</head>
<body>
<main class="sheet">
  <section class="card front">
    <div class="corner-square"></div>
    <div class="name-block">
      <p class="name">MARK ELLISON</p>
      <p class="title">Director</p>
    </div>
    <div class="brand"><span class="mark"></span><span>CREWWELL</span></div>
    <ul class="contacts">
      <li><svg viewBox="0 0 24 24"><path d="M6.6 10.8a15.1 15.1 0 0 0 6.6 6.6l2.2-2.2a1 1 0 0 1 1-.25 11.4 11.4 0 0 0 3.6.57 1 1 0 0 1 1 1V20a1 1 0 0 1-1 1A17 17 0 0 1 3 4a1 1 0 0 1 1-1h3.5a1 1 0 0 1 1 1c0 1.25.2 2.45.57 3.57a1 1 0 0 1-.25 1z"/></svg>(555)014 2290</li>
      <li><svg viewBox="0 0 24 24"><path d="M2 5h20v14H2z M2 5l10 8 10-8" /></svg>info@crewwellhealth.com</li>
      <li><svg viewBox="0 0 24 24"><circle cx="12" cy="12" r="10"/></svg>www.crewwellhealth.com</li>
    </ul>
  </section>
  <section class="card back">
    <div class="brand"><span>CREWWELL</span></div>
  </section>
</main>
</body>
</html>
```